Webdesign für HALDEN STAHLWERK
Zielgruppe
Valkorin ist Ihr leistungsstarker und zuverlässiger Partner im Bereich Metallverarbeitung. Seit unserer Firmengründung im Jahr 2001 ist unser inhabergeführtes Unternehmen in Gornau bei Chemnitz kontinuierlich gewachsen und beschäftigt derzeit 20 engagierte und qualifizierte Mitarbeiter.
Mit der Einweihung unserer neuen Fertigungshalle 2010 haben wir unsere Produktionsfläche auf 1.400 m2 vergrößert und können Ihnen nun einen noch umfassenderen Service anbieten.
Von der CNC-gesteuerten Teilefertigung bis zu modernsten Schweiß-, Schneid-, und Bearbeitungsanlagen – für die Realisierung Ihrer individuellen Wünsche steht uns ein innovativer Maschinenpark zur Verfügung. Wir fertigen zuverlässig und termingerecht nach Ihren Plänen oder übernehmen bei Bedarf auch die gesamte Abwicklung Ihres Projektes – alles made in germany!
Das Unternehmen spricht ausschließlich B2B Kunden an.
Die Hauptleistungsbereiche sind:
- Stahl- und Palettenbau
- Blechbearbeitung
- Edelstahlbearbeitung
- Mechanische Fertigung
Aufgabenstellung
- Mitlaufende Kontaktleiste
- Integration der Social Media Kanäle
- Sehr modernes Auftreten
- Industrielles Design
- Verlinkung zum Partnerunternehmen https://www.valkorin-beispiel.de/ias/index.html

```html
<!DOCTYPE html>
<html lang="de">
<head>
<meta charset="utf-8">
<title>Valkorin – Metallverarbeitung</title>
<link rel="stylesheet" href="https://fonts.googleapis.com/css2?family=Sora:wght@400;500;600&family=Inter:wght@400;500;600&display=swap">
<style>
:root{
  --navy:#141a4a;
  --blue:#3d8fe0;
  --band:#1d3b74;
  --band-dark:#142a5a;
  --footer:#0b1524;
  --gray:#f3f3f4;
  --text:#1a1a22;
  --muted:#8a8f99;
  --line:#e2e4e8;
}
*{box-sizing:border-box;margin:0;padding:0}
html,body{width:1200px;height:4418px;overflow:hidden}
body{position:relative;background:#fff;font-family:Inter,sans-serif;color:var(--text)}
.abs{position:absolute}
.h-font{font-family:Sora,sans-serif}
.label{position:absolute;font-size:10px;letter-spacing:1.6px;text-transform:uppercase;color:var(--blue);font-weight:500}
.h2{position:absolute;font-family:Sora,sans-serif;font-size:24px;font-weight:600;color:var(--text)}
.btn{position:absolute;display:flex;align-items:center;justify-content:center;gap:8px;font-size:12px;font-weight:500;border:1.5px solid var(--navy);color:var(--navy);background:#fff}
.rule{position:absolute;height:1px;background:var(--line)}
/* top bar + header */
.topbar{top:0;left:0;width:1200px;height:29px;font-size:9px;letter-spacing:.8px;color:#444}
.topbar span{position:absolute;top:10px}
.dot{position:absolute;top:9px;width:11px;height:11px;border-radius:50%;background:#9aa0aa}
.logo{position:absolute;font-family:Sora,sans-serif;font-weight:600;font-size:32px;letter-spacing:-1px}
.nav{position:absolute;top:58px;font-size:12px;font-weight:500;color:#222}
/* hero */
.hero{top:105px;left:0;width:1160px;height:495px;background:linear-gradient(120deg,#2a2f38,#4a4d52 45%,#3a3126 70%,#1d1f24);clip-path:polygon(0 0,100% 0,100% 75%,1074px 100%,0 100%)}
.hero-title{position:absolute;top:262px;left:0;width:1200px;text-align:center;color:#fff;font-family:Sora,sans-serif;font-weight:500;font-size:36px;line-height:40px}
.side-text{position:absolute;left:1100px;top:470px;transform:rotate(-90deg);transform-origin:left top;color:#fff;font-size:9px;letter-spacing:1.6px;white-space:nowrap}
.quick{position:absolute;left:1152px;width:48px;height:52px;background:var(--blue);display:flex;align-items:center;justify-content:center}
/* cards */
.svc{position:absolute;top:790px;width:211px;height:283px}
.svc .ph{position:absolute;top:0;left:0;width:211px;height:252px;clip-path:polygon(0 0,88% 0,100% 12%,100% 100%,0 100%)}
.svc .tag{position:absolute;left:0;bottom:0;width:157px;height:57px;background:var(--navy);color:#fff;font-size:11px;letter-spacing:1.4px;font-weight:500;padding:16px 15px;line-height:14px}
.news{position:absolute;top:1342px;width:288px}
.news .ph{height:211px;clip-path:polygon(0 0,92% 0,100% 10%,100% 100%,0 100%)}
.pill{margin-top:15px;display:inline-block;background:var(--blue);color:#fff;font-size:8px;padding:6px 11px;border-radius:12px}
.news h3{margin-top:10px;font-size:11px;font-weight:600;letter-spacing:.3px}
.news p{margin-top:10px;font-size:8px;color:#aab}
/* facts */
.gray-panel{top:1819px;left:0;width:809px;height:821px;background:var(--gray);clip-path:polygon(0 0,745px 0,809px 64px,809px 384px,0 384px)}
.gray-strip{top:2203px;left:0;width:151px;height:484px;background:var(--gray)}
.fact{position:absolute;top:2015px;width:200px;text-align:center}
.fact b{display:block;font-family:Sora,sans-serif;font-weight:500;font-size:56px;color:var(--blue);letter-spacing:-1px}
.fact span{display:block;margin-top:10px;font-size:10px;letter-spacing:1.4px;font-weight:600}
.vdiv{position:absolute;top:2028px;width:1px;height:75px;background:#d8dadf}
/* footer */
.footer{top:3838px;left:0;width:1200px;height:499px;background:var(--footer);color:#fff}
.fh{position:absolute;font-size:10px;letter-spacing:1.5px;color:var(--blue);font-weight:600}
.fl{position:absolute;font-size:11px;line-height:29px}
</style>
</head>
<body>

<div class="abs topbar">
  <span style="left:41px">T: +49 3700 / 240 118 6</span>
  <span style="left:176px">E: INFO@VALKORIN-BEISPIEL.DE</span>
  <i class="dot" style="left:990px"></i><i class="dot" style="left:1021px"></i><i class="dot" style="left:1052px"></i><i class="dot" style="left:1084px"></i><i class="dot" style="left:1115px"></i><i class="dot" style="left:1147px"></i>
</div>

<div class="logo" style="left:41px;top:46px;color:#111">VALKORIN</div>
<div class="nav" style="left:530px">Home</div>
<div class="nav" style="left:591px">Leistungen</div>
<div class="nav" style="left:683px">Produkte</div>
<div class="nav" style="left:763px">Fertigung</div>
<div class="nav" style="left:846px">Qualifikation</div>
<div class="nav" style="left:947px">Über Uns</div>
<div class="abs" style="left:1029px;top:52px;width:1px;height:26px;background:var(--line)"></div>
<div class="btn" style="left:1063px;top:46px;width:97px;height:39px;border-color:var(--blue);color:var(--blue)">Kontakt →</div>

<div class="abs hero" role="img" aria-label="Foto: CNC-Fräsmaschine bei der Metallbearbeitung mit Funkenflug"></div>
<h1 class="hero-title">Ihr zuverlässiger Partner im<br>Bereich der Metallverarbeitung</h1>
<div class="btn" style="left:438px;top:365px;width:146px;height:40px;border:none;font-size:11px">Angebot einholen →</div>
<div class="btn" style="left:605px;top:365px;width:157px;height:40px;background:transparent;border-color:#fff;color:#fff;font-size:11px">Jetzt mehr erfahren →</div>
<div class="abs" style="left:1114px;top:148px;width:1px;height:310px;background:rgba(255,255,255,.4)"></div>
<div class="side-text">YOUR PARTNER OF EXCELLENCE IN METALWORK</div>
<div class="quick" style="top:269px"><svg width="18" height="18" viewBox="0 0 24 24" fill="none" stroke="#fff" stroke-width="1.6"><path d="M22 2 11 13M22 2l-7 20-4-9-9-4z"/></svg></div>
<div class="quick" style="top:323px"><svg width="18" height="18" viewBox="0 0 24 24" fill="none" stroke="#fff" stroke-width="1.6"><path d="M22 16.9v3a2 2 0 0 1-2.2 2 19.8 19.8 0 0 1-8.6-3.1 19.5 19.5 0 0 1-6-6A19.8 19.8 0 0 1 2.1 4.2 2 2 0 0 1 4.1 2h3a2 2 0 0 1 2 1.7c.1 1 .4 1.9.7 2.8a2 2 0 0 1-.5 2.1L8 9.9a16 16 0 0 0 6 6l1.3-1.3a2 2 0 0 1 2.1-.4c.9.3 1.8.6 2.8.7a2 2 0 0 1 1.7 2z"/></svg></div>
<div class="quick" style="top:378px"><svg width="18" height="18" viewBox="0 0 24 24" fill="none" stroke="#fff" stroke-width="1.6"><path d="M3 21h18M5 21V10l4-2v13M9 21V6l5-3v18M14 21V9l5 2v10"/></svg></div>

<!-- Leistungen -->
<div class="label" style="left:151px;top:700px">Leistungen</div>
<div class="h2" style="left:151px;top:718px">Unsere Leistungsbereiche</div>
<div class="rule" style="left:510px;top:734px;width:533px"></div>
<div class="svc" style="left:151px"><div class="ph" role="img" aria-label="Foto: Laserschneiden von Stahlplatten" style="background:linear-gradient(160deg,#3a3f48,#1f2228 60%,#6b4a2a)"></div><div class="tag">STAHL- UND<br>PALETTENBAU</div></div>
<div class="svc" style="left:381px"><div class="ph" role="img" aria-label="Foto: Blechbearbeitung mit Funkenflug" style="background:linear-gradient(160deg,#2a2a3a,#6a2a3a 55%,#d0704a)"></div><div class="tag">BLECH-<br>BEARBEITUNG</div></div>
<div class="svc" style="left:610px"><div class="ph" role="img" aria-label="Foto: Arbeiter mit Helm in einer Edelstahlanlage" style="background:linear-gradient(160deg,#c9ccd0,#8f959d 60%,#5a6272)"></div><div class="tag">EDELSTAHL-<br>BEARBEITUNG</div></div>
<div class="svc" style="left:838px"><div class="ph" role="img" aria-label="Foto: Facharbeiter mit Schutzbrille an einer Maschine" style="background:linear-gradient(160deg,#5a6472,#2f3a4c 55%,#8a8f98)"></div><div class="tag">MECHANISCHE<br>FERTIGUNG</div></div>
<div class="btn" style="left:492px;top:1113px;width:182px;height:39px;font-size:11px">Alle Leistungen ansehen →</div>

<!-- News -->
<div class="label" style="left:151px;top:1253px">Neuigkeiten rund um die Metallverarbeitung</div>
<div class="h2" style="left:151px;top:1271px">Aktuelles &amp; Neuigkeiten</div>
<div class="rule" style="left:470px;top:1286px;width:460px"></div>
<div class="abs" style="left:960px;top:1265px;width:40px;height:41px;border:1px solid var(--line);display:flex;align-items:center;justify-content:center;color:#bbb;font-size:14px">←</div>
<div class="abs" style="left:1010px;top:1265px;width:40px;height:41px;background:#eef0f3;display:flex;align-items:center;justify-content:center;color:#333;font-size:14px">→</div>
<div class="news" style="left:151px"><div class="ph" role="img" aria-label="Foto: Laserschneidanlage im Betrieb" style="background:linear-gradient(160deg,#444a55,#1e2128 60%,#7a5430)"></div><span class="pill">Categorytag</span><h3>LOREM IPSUM DOLOR SIT AMET</h3><p>vom 24. September 2023</p></div>
<div class="news" style="left:456px"><div class="ph" role="img" aria-label="Foto: geschwungene Metalllamellen" style="background:linear-gradient(100deg,#2b2f36,#a8acb2 50%,#e4e6e8)"></div><span class="pill">Categorytag</span><h3>LOREM IPSUM DOLOR SIT AMET</h3><p>vom 24. September 2023</p></div>
<div class="news" style="left:763px"><div class="ph" role="img" aria-label="Foto: Metallfassade mit gefalteten Paneelen" style="background:linear-gradient(100deg,#6d7580,#c3c8cf 50%,#9aa2ac)"></div><span class="pill">Categorytag</span><h3>LOREM IPSUM DOLOR SIT AMET</h3><p>vom 24. September 2023</p></div>
<div class="btn" style="left:512px;top:1680px;width:155px;height:38px;font-size:11px">Alle News ansehen →</div>

<!-- Zahlen -->
<div class="abs gray-panel"></div>
<div class="abs gray-strip"></div>
<div class="label" style="left:151px;top:1911px">Fakten und Zahlen</div>
<div class="h2" style="left:151px;top:1929px">VALKORIN in Zahlen</div>
<div class="fact" style="left:149px"><b>22</b><span>JAHRE EXPERTISE</span></div>
<div class="vdiv" style="left:351px"></div>
<div class="fact" style="left:365px"><b>1.400</b><span>M² PRODUKTIONSFLÄCHE</span></div>
<div class="vdiv" style="left:581px"></div>
<div class="fact" style="left:594px"><b>20</b><span>ENGAGIERTE MITARBEITER</span></div>
<div class="fact" style="left:843px"><b>100%</b><span>MADE IN GERMANY</span></div>

<div class="abs" role="img" aria-label="Foto: Mechaniker richtet ein Werkstück in einer CNC-Maschine ein" style="left:151px;top:2203px;width:1049px;height:484px;background:linear-gradient(110deg,#cfd6de,#8c98a6 35%,#3a4656 60%,#c9a77a 85%,#2c3440);clip-path:polygon(0 0,100% 0,100% 100%,110px 100%,0 380px)"></div>
<div class="abs" style="left:405px;top:2563px;width:795px;height:248px;background:var(--navy)"></div>
<div class="label" style="left:465px;top:2604px">Ihr zuverlässiger Partner</div>
<div class="abs h-font" style="left:465px;top:2624px;color:#fff;font-size:23px;font-weight:500;line-height:33px">Wir vereinen Qualität und<br>Kundenzufriedenheit</div>
<div class="abs" style="left:790px;top:2606px;width:335px;color:#c8cce0;font-size:10px;line-height:17px">Lorem ipsum dolor sit amet consectetur. Risus risus dui commodo posuere aenean ac mauris sed. Morbi aliquam tincidunt nibh leo. Quam ipsum sapien mauris pharetra id convallis ac nunc venenatis. Blandit viverra nunc enim sagittis accumsan habitant. Leo elit tellus sapien arcu congue sit malesuada id.<br><br>Vestibulum augue tempus sed scelerisque at tellus. Diam magna commodo donec odio. Quisque eget ridiculus risus placerat fringilla congue sit dolor. Penatibus massa urna egestas velit in tortor nec molestie tincidunt.</div>

<!-- Partner -->
<div class="rule" style="left:151px;top:2919px;width:892px"></div>
<div class="label" style="left:151px;top:2983px">Partnerunternehmen</div>
<div class="h2" style="left:151px;top:3001px">Industrie- und Anlagenservice</div>
<div class="abs" style="left:151px;top:3050px;width:510px;color:var(--blue);font-size:10.5px;line-height:17px">Lorem ipsum dolor sit amet consectetur. Risus risus dui commodo posuere aenean ac mauris sed. Morbi aliquam tincidunt nibh leo. Quam ipsum sapien mauris pharetra id convallis ac nunc venenatis. Blandit viverra nunc enim sagittis accumsan habitant. Leo elit tellus sapien arcu congue sit malesuada id.</div>
<div class="abs" style="left:790px;top:3030px;display:flex;align-items:center;gap:12px">
  <span style="width:44px;height:44px;background:#1d4f9c;display:block"></span>
  <span style="font-size:19px;font-weight:500;color:#1d4f9c;line-height:22px">Kessler<br>Anlagenservice</span>
</div>

<!-- Kontakt -->
<div class="abs" style="left:151px;top:3235px;width:1049px;height:372px;background:var(--band)"></div>
<div class="abs" style="left:591px;top:3607px;width:609px;height:127px;background:var(--band-dark)"></div>
<div class="abs" role="img" aria-label="Foto: lächelnder Techniker mit Schutzhelm an einem Bedienpult" style="left:0;top:3332px;width:591px;height:506px;background:linear-gradient(120deg,#d6dade,#9aa4b0 40%,#2a3858 70%,#3d4650);clip-path:polygon(0 0,530px 0,591px 61px,591px 100%,0 100%)"></div>
<div class="abs h-font" style="left:667px;top:3334px;color:#fff;font-size:23px;font-weight:500">Kontakt</div>
<div class="abs" style="left:667px;top:3368px;color:#b5c4e0;font-size:11px">So erreichen Sie uns</div>
<svg class="abs" style="left:667px;top:3441px" width="20" height="20" viewBox="0 0 24 24" fill="none" stroke="#fff" stroke-width="1.5"><path d="M22 16.9v3a2 2 0 0 1-2.2 2 19.8 19.8 0 0 1-8.6-3.1 19.5 19.5 0 0 1-6-6A19.8 19.8 0 0 1 2.1 4.2 2 2 0 0 1 4.1 2h3a2 2 0 0 1 2 1.7c.1 1 .4 1.9.7 2.8a2 2 0 0 1-.5 2.1L8 9.9a16 16 0 0 0 6 6l1.3-1.3a2 2 0 0 1 2.1-.4c.9.3 1.8.6 2.8.7a2 2 0 0 1 1.7 2z"/></svg>
<div class="abs" style="left:700px;top:3436px;color:#fff;font-size:16px;font-weight:500">+49 3700 / 240 118 00</div>
<div class="abs" style="left:700px;top:3460px;color:var(--blue);font-size:9px;letter-spacing:1px">MO-FR &nbsp;&nbsp;08:00 - 18:00</div>
<div class="abs" style="left:667px;top:3488px;width:400px;height:1px;background:rgba(255,255,255,.25)"></div>
<svg class="abs" style="left:667px;top:3508px" width="20" height="20" viewBox="0 0 24 24" fill="none" stroke="#fff" stroke-width="1.5"><path d="M22 2 11 13M22 2l-7 20-4-9-9-4z"/></svg>
<div class="abs" style="left:700px;top:3503px;color:#fff;font-size:16px;font-weight:500">info@valkorin-beispiel.de</div>
<div class="abs" style="left:700px;top:3527px;color:var(--blue);font-size:9px">Wir antworten meist binnen 24 Stunden</div>
<div class="abs" style="left:667px;top:3652px;color:#fff;font-size:11px;line-height:16px">Oder nutzen Sie<br>unser <b>Kontaktformular</b></div>
<div class="btn" style="left:881px;top:3650px;width:168px;height:39px;background:transparent;border-color:#fff;color:#fff;font-size:11px">Zum Kontaktformular →</div>

<!-- Footer -->
<div class="abs footer">
  <div class="logo" style="left:151px;top:112px;color:#fff">VALKORIN</div>
  <div class="abs" style="left:151px;top:186px;font-size:10px;line-height:18px"><b>Valkorin GmbH</b><br>Musterstraße 1<br>12345 Musterstadt<br>Deutschland</div>
  <div class="abs" style="left:151px;top:270px;width:265px;font-size:10px;line-height:17px;color:#c9cdd6">Lorem ipsum dolor sit amet consectetur. Dolor cras eget a volutpat ullamcorper facilisis. Viverra aliquam ac aliquet aliquet odio in aliquet.</div>
  <div class="fh" style="left:454px;top:122px">SEITEN</div>
  <div class="fl" style="left:454px;top:142px">Leistungen<br>Produkte<br>Fertigung<br>Qualifikation<br>Über uns</div>
  <div class="fh" style="left:609px;top:122px">RECHTLICHES</div>
  <div class="fl" style="left:609px;top:142px">Impressum<br>Datenschutzerklärung</div>
  <div class="fh" style="left:609px;top:230px">KONTAKT &amp; SONSTIGES</div>
  <div class="fl" style="left:609px;top:250px">FAQ<br>Kontakt<br>Links</div>
  <div class="fh" style="left:838px;top:122px">KONTAKTINFORMATIONEN</div>
  <div class="abs" style="left:838px;top:162px;font-size:10px;line-height:16px">Telefon:<br><span style="color:var(--blue)">+49 3700 / 240 118 00</span></div>
  <div class="abs" style="left:838px;top:222px;font-size:10px;line-height:16px">E-Mail:<br><span style="color:var(--blue)">info@valkorin-beispiel.de</span></div>
  <div class="abs" style="left:838px;top:256px;width:82px;height:34px;border:1.5px solid #fff;border-radius:17px;display:flex;align-items:center;justify-content:center;font-size:11px">Kontakt</div>
  <div class="abs" style="left:151px;top:375px;width:900px;height:1px;background:rgba(255,255,255,.15)"></div>
  <div class="abs" style="left:151px;top:400px;font-size:10px">Copyright © 2023 valkorin-beispiel.de</div>
  <i class="abs" style="left:842px;top:399px;width:16px;height:16px;border-radius:50%;background:var(--blue)"></i>
  <i class="abs" style="left:881px;top:399px;width:16px;height:16px;border-radius:50%;background:var(--blue)"></i>
  <i class="abs" style="left:919px;top:399px;width:16px;height:16px;border-radius:50%;background:var(--blue)"></i>
  <i class="abs" style="left:957px;top:399px;width:16px;height:16px;border-radius:50%;background:var(--blue)"></i>
  <i class="abs" style="left:995px;top:399px;width:16px;height:16px;border-radius:50%;background:var(--blue)"></i>
  <i class="abs" style="left:1034px;top:399px;width:16px;height:16px;border-radius:50%;background:var(--blue)"></i>
</div>

</body>
</html>
```